Catalogue Design Project

We need a catalog design for a new private university called Redwell Institute Bayshore (see website www.rwi-bs.org). The catalog should be about 30 pages maximum and will include items such as General Information, Academic schedule, department descriptions, program descriptions, course descriptions, school policies, student services, admissions, San diego Lifestyle, etc.
I will provide the text but I need a professional design with regard to page layouts. I have provided some examples.
Ok, i posted the catalog content, just missing course descriptions.
Target Market(s)
Young Professionals, Foreign Students
Industry/Entity Type
University
Look and feel
Each slider illustrates characteristics of the customer's brand and the style your logo design should communicate.

```html
<!DOCTYPE html>
<html lang="en">
<head>
<meta charset="utf-8">
<title>Tax Audit Preparation Certificate – Redwell Institute Bayshore</title>
<link href="https://fonts.googleapis.com/css2?family=Carlito:ital,wght@0,400;0,700&display=swap" rel="stylesheet">
<style>
  :root {
    --ink: #1a1a1a;
    --brand-blue: #3f6f9f;
    --rule-blue: #5b87b3;
    --footer-grey: #8a8a8a;
    --paper: #ffffff;
    --book-warm: #d8c49a;
    --book-light: #efe6cf;
    --dot-grey: #b5b5b5;
  }
  html, body {
    margin: 0;
    padding: 0;
    overflow: hidden;
    background: var(--paper);
  }
  .page {
    position: relative;
    width: 927px;
    height: 1200px;
    overflow: hidden;
    background: var(--paper);
    font-family: "Carlito", "Calibri", sans-serif;
    color: var(--ink);
  }
  .brand-pattern {
    position: absolute;
    left: 60px;
    top: 36px;
    width: 152px;
    height: 34px;
    border-radius: 17px;
    background: linear-gradient(90deg, var(--brand-blue), var(--dot-grey) 40%, var(--dot-grey) 80%, var(--brand-blue));
    opacity: 0.85;
  }
  .header-image {
    position: absolute;
    right: 0;
    top: 0;
    width: 352px;
    height: 103px;
    background: linear-gradient(90deg, rgba(255,255,255,1) 0%, var(--book-light) 35%, var(--book-warm) 75%, #e6dcc6 100%);
  }
  .header-rule {
    position: absolute;
    left: 0;
    top: 102px;
    width: 927px;
    height: 2px;
    background: var(--rule-blue);
  }
  .section-tab {
    position: absolute;
    left: 530px;
    top: 102px;
    width: 397px;
    height: 40px;
  }
  .section-tab-label {
    position: absolute;
    left: 572px;
    top: 104px;
    width: 340px;
    height: 38px;
    line-height: 38px;
    color: #fff;
    font-size: 28px;
    letter-spacing: 0.5px;
    text-align: right;
  }
  .program-title {
    position: absolute;
    left: 0;
    top: 203px;
    width: 927px;
    margin: 0;
    text-align: center;
    font-size: 25px;
    font-weight: 700;
  }
  .program-body {
    position: absolute;
    left: 79px;
    width: 770px;
    margin: 0;
    font-size: 19.5px;
    line-height: 37px;
    text-align: justify;
  }
  .program-intro { top: 241px; }
  .program-facts { top: 493px; }
  .program-course { top: 603px; }
  .program-outcome { top: 712px; }
  .program-body p { margin: 0; }
  .label { font-weight: 700; }
  .subhead { text-decoration: underline; }
  .footer-rule {
    position: absolute;
    left: 0;
    top: 1153px;
    width: 927px;
    height: 1px;
    background: var(--rule-blue);
  }
  .footer-folio {
    position: absolute;
    right: 36px;
    top: 1170px;
    font-size: 13.5px;
    color: var(--footer-grey);
    letter-spacing: 0.3px;
  }
</style>
</head>
<body>
<div class="page">
  <div class="brand-pattern" role="img" aria-label="Row of blue and grey dots forming a decorative header pattern"></div>
  <div class="header-image" role="img" aria-label="Faded photograph of an open old book"></div>
  <div class="header-rule"></div>
  <svg class="section-tab" viewBox="0 0 397 40" aria-hidden="true">
    <polygon points="0,0 397,0 397,40 38,40" fill="#3f6f9f"/>
  </svg>
  <div class="section-tab-label">CERTIFICATE PROGRAMS</div>

  <h1 class="program-title">Tax Audit Preparation Certificate</h1>

  <div class="program-body program-intro">
    <p>Learn how to prepare individual or corporate tax filing correctly to avoid being audited by the IRS.&nbsp;&nbsp;&nbsp;&nbsp; Taught by instructors who are also current agents with the Internal Revenue Service, students who are already in the midst of being audited or have just received an audit notice, will receive first hand knowledge of how best make to avoid the process or make as painless as possible.&nbsp; Students will learn what kind of audits are possible, what their rights are, and most importantly how to prepare the requested financial documents in the manner that satisfies IRS requirements for present and future tax filings.</p>
  </div>

  <div class="program-body program-facts">
    <p><span class="label">Hours:</span> 6 hours per week</p>
    <p><span class="label">Length:</span> 8 weeks per course</p>
  </div>

  <div class="program-body program-course">
    <p class="subhead">Course:</p>
    <p>ACCT 640 Tax Audit Preparation</p>
  </div>

  <div class="program-body program-outcome">
    <p class="subhead">Learning Outcome:</p>
    <p>Students will understand how to file personal and corporate taxes such that the chances of an audit are low.&nbsp; Students who take the class to better inform themselves for a current audit will gain the training on how to fill out and submit required documents to quicken the process and decrease tax liability.</p>
  </div>

  <div class="footer-rule"></div>
  <div class="footer-folio">14::: REDWELL INSTITUTE BAYSHORE</div>
</div>
</body>
</html>
```